Modernize and improve usability of our webpage www.lernwandel.ch (4 languages, mostly static content)

Need to modernize and freshen up the webpages of our association: www.lernwandel.ch We offer apprenticeship exchanges within Switzerland and abroad. Young people can inform and enroll online. We do the matchmaking with work locations and organize logistics, stay overs etc.
The webpage needs to be in 4 languages (German, French, Italian and English). The main pages will be:
- Landing page: what we do, targeted to our apprentices / young people who enroll for the stages.
- Sup-Page: Registration form for interested apprentices to sign up for the program
- Sub-Page "Company", the firms who would like to send their apprentices on a internship and info on how to join the program
- Sub-Page "Host Family", private people who would be interested in hosting the apprentices (for free) during the stages. Find out about the reqiurements for the host families
- Sub-Page "About Us", who we are, executive team, board of director, our sponsor "Falkner Circle Switzerland"
- Footer: contact (E-Mail, Telephone, WhatsApp), Bank details (IBAN Number), Partnerlogo of Falkner-Circle (see uploaded jpg), Social-Media Links (Facebook, LinkedIn)

Target Market(s)

Young people looking for a "apprenticeship" stage within Switzerland or going from Switzerland abroad

Industry/Entity Type

Apprenticeships: cooks, builders, craftsman, office support, etc.

Number of Pages Required

5+ page

Font styles to use
Other font styles liked:
• Lato (sans serif)

Requirements
Must have
• use colors shown on uploaded PDF-Slides: Make the BLUE the MAIN color, the ORANGE as a secondary color
Nice to have
• Forms using e.g. google forms or survey-monkey forms (external links, no code). Matching & appealing visuals showing young apprentices (can use stock photos)

```html
<!DOCTYPE html>
<html lang="en">
<head>
<meta charset="utf-8">
<title>Lernwandel – Apprenticeship Exchange</title>
<link href="https://fonts.googleapis.com/css2?family=Poppins:wght@500;600;700&family=Open+Sans:wght@400;500;600;700&display=swap" rel="stylesheet">
<style>
:root{
  --navy:#1d3a5c;
  --topbar:#1f2a38;
  --orange:#f25c05;
  --ink:#1f3b5e;
  --text:#7a8290;
  --light:#f4f4f4;
  --white:#fff;
  --testi:#1b3552;
  --quote:#2a4563;
}
*{margin:0;padding:0;box-sizing:border-box}
html,body{width:1200px;height:4841px;overflow:hidden}
body{position:relative;font-family:"Open Sans",sans-serif;color:var(--text);background:var(--white)}
.abs{position:absolute}
.btn{position:absolute;background:var(--orange);color:#fff;font-family:"Poppins",sans-serif;font-weight:600;font-size:15px;display:flex;align-items:center;justify-content:center;gap:12px}
.label{position:absolute;color:var(--orange);font-size:11px;font-weight:600;text-decoration:underline;text-underline-offset:3px;letter-spacing:.3px}
.photo{position:absolute}

.topbar{position:absolute;left:0;top:0;width:1200px;height:47px;background:var(--topbar);color:#d7dbe1;font-size:13px}
.topbar span{position:absolute;top:15px}
.social-dot{position:absolute;top:18px;width:11px;height:11px;border-radius:50%;background:#b8c0cb}

.logo{position:absolute;color:var(--orange);font-family:"Poppins",sans-serif;font-weight:600;white-space:nowrap}
.hinfo{position:absolute;font-size:13px;line-height:22px;color:var(--ink)}
.hinfo small{display:block;color:var(--text);font-size:13px}
.nav{position:absolute;left:79px;top:154px;width:986px;height:68px;background:#fff;z-index:3}
.nav a{position:absolute;top:25px;font-size:13px;color:var(--text);text-decoration:none}
.nav-call{position:absolute;left:1065px;top:154px;width:73px;height:68px;background:var(--navy);z-index:3;display:flex;align-items:center;justify-content:center}

.hero-bg{position:absolute;left:0;top:154px;width:1200px;height:794px;background:linear-gradient(120deg,#2e3f52 0%,#4a5b6c 45%,#35465a 100%)}
.hero-tag{position:absolute;left:100px;top:451px;width:266px;height:41px;background:var(--navy);border-left:4px solid var(--orange);color:#fff;font-family:"Poppins",sans-serif;font-weight:600;font-size:20px;padding:7px 0 0 18px}
.hero-title{position:absolute;left:100px;top:515px;color:#fff;font-family:"Poppins",sans-serif;font-size:52px;font-weight:600;white-space:nowrap}
.hero-p{position:absolute;left:100px;top:608px;width:500px;color:#fff;font-size:17px;line-height:26px}

.about-title{position:absolute;left:83px;top:1096px;font-size:40px;font-weight:600;color:var(--ink);line-height:53px}
.about-sub{position:absolute;left:83px;top:1226px;font-size:22px;font-weight:600;color:var(--ink)}
.about-p{position:absolute;left:83px;top:1274px;width:505px;font-size:12.5px;line-height:21.5px}
.badge{position:absolute;left:822px;top:1237px;width:76px;height:76px;border-radius:50%;background:var(--navy);border:3px solid var(--orange)}

.services{left:0;top:1559px;width:1200px;height:649px;background:var(--light)}
.sec-title{position:absolute;font-weight:600;color:var(--ink);font-size:40px}
.card{position:absolute;top:1769px;width:317px;height:353px;background:linear-gradient(180deg,#4f5d6a 0%,#39495c 55%,#1f3a60 100%)}
.card h4{position:absolute;left:28px;top:230px;color:#fff;font-weight:700;font-size:24px;white-space:nowrap}
.card .dot{position:absolute;left:22px;top:233px;width:14px;height:14px;border-radius:50%;background:var(--orange)}
.card .go{position:absolute;left:28px;top:281px;width:46px;height:46px;border-radius:50%;background:rgba(255,255,255,.25);display:flex;align-items:center;justify-content:center}

.experts{left:0;top:2208px;width:1200px;height:384px;background:linear-gradient(90deg,#1f3b60 0%,#2c4b72 60%,#1f3b60 100%)}
.experts-title{position:absolute;left:88px;top:2316px;color:#fff;font-size:38px;font-weight:600;line-height:54px}
.feature{position:absolute;top:2321px;width:233px;height:365px;background:#fff;box-shadow:0 4px 18px rgba(0,0,0,.1);text-align:center}
.feature .ic{display:block;margin:30px auto 0;width:56px;height:56px}
.feature h4{margin-top:18px;font-weight:500;font-size:20px;color:var(--ink)}
.feature p{margin:22px auto 0;width:188px;font-size:12.5px;line-height:18.5px}
.feature .more{position:absolute;left:0;right:0;bottom:38px;font-size:13px;font-weight:700;color:var(--ink)}

.why-item{position:absolute}
.why-item h4{font-weight:500;font-size:20px;color:var(--ink)}
.why-item p{font-size:12.5px;line-height:18px;margin-top:8px;width:200px}
.why-ic{position:absolute;width:82px;height:82px;border-radius:50%;background:#fff;box-shadow:0 3px 14px rgba(0,0,0,.1);display:flex;align-items:center;justify-content:center}

.testi{left:0;top:3334px;width:1200px;height:535px;background:var(--testi)}
.quote{position:absolute;top:3548px;width:323px;height:216px;background:var(--quote)}
.quote .qm{position:absolute;left:140px;top:2px;color:var(--orange);font-family:"Poppins",sans-serif;font-weight:700;font-size:60px;line-height:60px}
.quote p{position:absolute;left:33px;top:38px;width:262px;color:#fff;font-size:12.5px;line-height:19px}
.quote .av{position:absolute;left:28px;top:143px;width:48px;height:48px;border-radius:50%;background:linear-gradient(#dcd2c8,#a89888)}
.quote .nm{position:absolute;left:94px;top:145px;color:#fff;font-size:15px}
.quote .loc{position:absolute;left:94px;top:167px;color:#8b9aae;font-size:15px}
.dots{position:absolute;top:3789px;left:567px;display:flex;gap:6px;align-items:center}
.dots i{width:6px;height:6px;border-radius:50%;background:#9fb0c6;display:block}
.dots i.on{width:9px;height:9px;background:var(--orange)}

.cinfo{position:absolute;left:182px;font-size:12px;line-height:21px}
.cinfo b{display:block;color:var(--ink);font-weight:600;font-size:12.5px}
.cicon{position:absolute;left:118px;width:38px;height:38px}
.form{position:absolute;left:597px;top:3976px;width:494px;height:569px;background:#fff;border-top:5px solid var(--navy);box-shadow:0 4px 24px rgba(0,0,0,.1);z-index:2}
.form h3{position:absolute;left:37px;top:50px;font-weight:600;font-size:23px;color:var(--ink)}
.form label{position:absolute;font-size:12px;font-weight:600;color:var(--ink)}
.field{position:absolute;border:1px solid #c9cfd8;border-radius:18px;font-size:11px;color:#9aa1ab;padding:12px 24px}
.field.area{border-radius:10px}

.fnav{position:absolute;left:257px;top:4695px;width:725px;height:56px;border-top:1px solid #4d6583;border-bottom:1px solid #4d6583}
.fnav span{position:absolute;top:18px;color:#fff;font-size:13px;transform:translateX(-50%);white-space:nowrap}
.fcontact{position:absolute;top:4613px;color:#fff;font-size:13px;line-height:19px}
.fdiv{position:absolute;top:4605px;width:1px;height:52px;background:#5a6f8c}
.sq{position:absolute;top:4786px;width:26px;height:26px;border:1px solid #9fb0c6}
</style>
</head>
<body>

<div class="topbar">
  <svg class="abs" style="left:77px;top:16px" width="14" height="14" viewBox="0 0 14 14"><circle cx="7" cy="7" r="6" fill="none" stroke="#f25c05" stroke-width="1.5"/><path d="M7 3.5V7l2.5 1.5" stroke="#f25c05" stroke-width="1.5" fill="none"/></svg>
  <span style="left:102px">Mon-Sat: 09am to 07:30pm</span>
  <svg class="abs" style="left:325px;top:17px" width="14" height="11" viewBox="0 0 14 11"><rect x=".75" y=".75" width="12.5" height="9.5" fill="none" stroke="#f25c05" stroke-width="1.5"/><path d="M1 1l6 5 6-5" fill="none" stroke="#f25c05" stroke-width="1.5"/></svg>
  <span style="left:347px">info@lernwandel.ch</span>
  <span style="left:871px;color:#6a7585">|</span>
  <span style="left:886px">Faqs</span>
  <span style="left:936px;color:#6a7585">|</span>
  <span style="left:952px">Pricing</span>
  <span style="left:1018px;color:#6a7585">|</span>
  <i class="social-dot" style="left:1036px"></i>
  <i class="social-dot" style="left:1060px"></i>
  <i class="social-dot" style="left:1084px"></i>
  <i class="social-dot" style="left:1108px"></i>
</div>

<div class="logo" style="left:145px;top:76px;font-size:33px;line-height:44px">lernwandel</div>
<svg class="abs" style="left:364px;top:82px" width="32" height="32" viewBox="0 0 32 32"><path d="M16 3a13 13 0 1 0 6.5 24.3L29 29l-1.8-6.3A13 13 0 0 0 16 3z" fill="none" stroke="#1d3a5c" stroke-width="2"/><circle cx="10" cy="16" r="1.6" fill="#f25c05"/><circle cx="16" cy="16" r="1.6" fill="#f25c05"/><circle cx="22" cy="16" r="1.6" fill="#f25c05"/></svg>
<div class="hinfo" style="left:412px;top:76px">+41-44-555-0190<small>Needhelp? Make a Call</small></div>
<svg class="abs" style="left:664px;top:82px" width="34" height="34" viewBox="0 0 34 34" fill="none" stroke="#1d3a5c" stroke-width="1.8"><circle cx="17" cy="17" r="14"/><ellipse cx="17" cy="17" rx="6" ry="14"/><path d="M3 17h28M5 10h24M5 24h24"/></svg>
<div class="hinfo" style="left:712px;top:76px">City, Country<small>123A Someplace</small></div>
<div class="btn" style="left:958px;top:75px;width:180px;height:49px;font-size:13px;border-radius:2px">Free Estimate
  <svg width="20" height="20" viewBox="0 0 20 20"><circle cx="10" cy="10" r="8.5" fill="none" stroke="#fff" stroke-width="1.6"/><path d="M8.5 6l4 4-4 4" fill="none" stroke="#fff" stroke-width="1.6"/></svg>
</div>

<div class="hero-bg" role="img" aria-label="Overhead photo of apprentices working together at a desk with laptops"></div>
<div class="nav">
  <a style="left:86px">Home</a>
  <a style="left:197px">About Us</a>
  <a style="left:309px">Services</a>
  <a style="left:448px">Solutions</a>
  <a style="left:560px">Team</a>
  <a style="left:658px">Gallery</a>
  <a style="left:759px">Contact Us</a>
</div>
<div class="nav-call">
  <svg width="34" height="34" viewBox="0 0 24 24" fill="none" stroke="#fff" stroke-width="1.4"><path d="M22 16.9v3a2 2 0 0 1-2.2 2 19.8 19.8 0 0 1-8.6-3.1 19.5 19.5 0 0 1-6-6A19.8 19.8 0 0 1 2.1 4.2 2 2 0 0 1 4.1 2h3a2 2 0 0 1 2 1.7c.1.9.4 1.9.7 2.8a2 2 0 0 1-.5 2.1L8 9.9a16 16 0 0 0 6 6l1.3-1.3a2 2 0 0 1 2.1-.4c.9.3 1.8.6 2.8.7a2 2 0 0 1 1.7 2z"/></svg>
</div>
<div class="hero-tag">We are leaders in</div>
<div class="hero-title">Apprenticeship Exchange</div>
<p class="hero-p">Lorem ipsum dolor sit amet, consectetur adipiscing elit, sed do eiusmod tempor incididunt ut labore et d</p>
<div class="btn" style="left:100px;top:689px;width:176px;height:53px">Read More</div>
<svg class="abs" style="left:0;top:800px" width="1200" height="150" viewBox="0 0 1200 150">
  <path d="M0 148 C300 140 700 100 1200 22 L1200 150 L0 150Z" fill="#fff"/>
  <path d="M0 128 C250 134 480 120 710 90" fill="none" stroke="#f25c05" stroke-width="16"/>
</svg>

<div class="label" style="left:83px;top:1063px">WHO WE ARE</div>
<div class="about-title">The team you can trust<br>to get the job done</div>
<div class="about-sub">Elevating Apprenticeship Exchange</div>
<p class="about-p">Lorem ipsum dolor sit amet, consectetur adipiscing elit, sed do eiusmod tempor incididunt ut labore et dolore magna aliqua. Ut enim ad minim veniam, quis nos trud exercitation ullamco laboris nisi ut aliquip ex ea commodo consequat. Duis aute irure dolor in reprehenderit in voluptate velit esse cillum dolore eu fugiat nulla pariatur. Excepteur sint occaecat cupidatat non proident, sunt in culpa qui officia deserunt mollit anim id est laborum.</p>
<div class="btn" style="left:83px;top:1433px;width:154px;height:43px;font-size:14px">Contact us
  <svg width="16" height="14" viewBox="0 0 16 14"><path d="M1 7h13M9 2l5 5-5 5" fill="none" stroke="#fff" stroke-width="1.8"/></svg></div>
<div class="photo" style="left:618px;top:1046px;width:237px;height:424px;background:linear-gradient(160deg,#4a5a6a,#8fa46a 55%,#3e4c5c)" role="img" aria-label="Young apprentice in a high-visibility vest writing at a workbench"></div>
<div class="photo" style="left:870px;top:1078px;width:238px;height:424px;background:linear-gradient(170deg,#c9c3bb,#ece8e3 60%,#d8d2ca)" role="img" aria-label="Smiling young apprentice in a white polo shirt"></div>
<div class="badge"></div>

<div class="abs services"></div>
<div class="label" style="left:87px;top:1619px">OUR SERVICES</div>
<div class="sec-title" style="left:87px;top:1651px">Services We Provide</div>
<div class="abs" style="left:943px;top:1670px;font-size:13px;color:var(--ink)">More Services</div>
<div class="abs" style="left:1076px;top:1660px;width:38px;height:38px;background:var(--orange);display:flex;align-items:center;justify-content:center"><svg width="12" height="14" viewBox="0 0 12 14"><path d="M3 2l6 5-6 5" fill="none" stroke="#fff" stroke-width="2"/></svg></div>
<div class="card" style="left:96px" role="img" aria-label="Smiling apprentice in an office">
  <span class="dot"></span><h4>Apprentice Matching</h4>
  <span class="go"><svg width="16" height="14" viewBox="0 0 16 14"><path d="M1 7h13M9 2l5 5-5 5" fill="none" stroke="#fff" stroke-width="1.8"/></svg></span>
</div>
<div class="card" style="left:443px" role="img" aria-label="Apprentice with ear protection working in a workshop">
  <span class="dot"></span><h4>Industry Networking</h4>
  <span class="go"><svg width="16" height="14" viewBox="0 0 16 14"><path d="M1 7h13M9 2l5 5-5 5" fill="none" stroke="#fff" stroke-width="1.8"/></svg></span>
</div>
<div class="card" style="left:789px" role="img" aria-label="Mentor guiding apprentices at a computer">
  <span class="dot"></span><h4>Career Guidance</h4>
  <span class="go"><svg width="16" height="14" viewBox="0 0 16 14"><path d="M1 7h13M9 2l5 5-5 5" fill="none" stroke="#fff" stroke-width="1.8"/></svg></span>
</div>

<div class="photo experts" role="img" aria-label="Team of colleagues talking in a bright office, blue tinted"></div>
<div class="experts-title">Leading<br>Experts</div>
<div class="btn" style="left:88px;top:2481px;width:156px;height:45px;font-size:14px">Contact us
  <svg width="16" height="14" viewBox="0 0 16 14"><path d="M1 7h13M9 2l5 5-5 5" fill="none" stroke="#fff" stroke-width="1.8"/></svg></div>

<div class="feature" style="left:353px">
  <svg class="ic" viewBox="0 0 56 56" fill="none" stroke="#f25c05" stroke-width="3"><path d="M22 34V12a4 4 0 0 1 8 0v14l10 3a5 5 0 0 1 3 6l-3 12H24l-8-10a4 4 0 0 1 6-5z"/><path d="M16 16a10 10 0 0 1 20 0"/></svg>
  <h4>Profesionalism</h4>
  <p>Lorem ipsum dolor sit amet, consectetur adipiscing elit, sed do eiusmod tem por incididunt ut labore et dolore magna aliqua. Ut enim ad minim veniam.</p>
  <div class="more">Read More &rarr;</div>
</div>
<div class="feature" style="left:612px">
  <svg class="ic" viewBox="0 0 56 56" fill="none" stroke="#f25c05" stroke-width="3"><path d="M8 48h40M12 48V34M20 48V28M28 48V36"/><circle cx="40" cy="14" r="5"/><path d="M34 48V26h12v22M10 24l12-10 8 4 6-6"/></svg>
  <h4>Expertise</h4>
  <p>Lorem ipsum dolor sit amet, consectetur adipiscing elit, sed do eiusmod tem por incididunt ut labore et dolore magna aliqua. Ut enim ad minim veniam.</p>
  <div class="more">Read More &rarr;</div>
</div>
<div class="feature" style="left:875px">
  <svg class="ic" viewBox="0 0 56 56" fill="none" stroke="#f25c05" stroke-width="3"><circle cx="28" cy="18" r="8"/><path d="M12 44v-4a10 10 0 0 1 10-10h12a10 10 0 0 1 10 10v4zM12 50h32"/></svg>
  <h4>Experience</h4>
  <p>Lorem ipsum dolor sit amet, consectetur adipiscing elit, sed do eiusmod tem por incididunt ut labore et dolore magna aliqua. Ut enim ad minim veniam.</p>
  <div class="more">Read More &rarr;</div>
</div>

<div class="label" style="left:574px;top:2739px">WHY US</div>
<div class="sec-title" style="left:0;width:1212px;text-align:center;top:2770px">Why Choose Us</div>
<div class="photo" style="left:434px;top:2908px;width:326px;height:326px;border-radius:50%;background:radial-gradient(circle at 50% 40%,#b9bcc2,#3d5a86 75%)" role="img" aria-label="Smiling mentor in a grey blazer with arms crossed"></div>

<div class="why-item" style="left:148px;top:2910px"><h4>Tailored Solutions</h4><p>Lorem ipsum dolor sit amet, consectetur adipiscing elit</p></div>
<div class="why-item" style="left:98px;top:3036px"><h4>Industry Connections</h4><p>Lorem ipsum dolor sit amet, consectetur adipiscing elit</p></div>
<div class="why-item" style="left:131px;top:3160px"><h4>Global Reach</h4><p>Lorem ipsum dolor sit amet, consectetur adipiscing elit</p></div>
<div class="why-item" style="left:892px;top:2910px"><h4>Skill Development</h4><p>Lorem ipsum dolor sit amet, consectetur adipiscing elit</p></div>
<div class="why-item" style="left:900px;top:3036px"><h4>Support System</h4><p>Lorem ipsum dolor sit amet, consectetur adipiscing elit</p></div>
<div class="why-item" style="left:877px;top:3160px"><h4>Connections</h4><p>Lorem ipsum dolor sit amet, consectetur adipiscing elit</p></div>

<div class="why-ic" style="left:353px;top:2904px"><svg width="32" height="32" viewBox="0 0 32 32" fill="none" stroke="#f25c05" stroke-width="2.4"><circle cx="16" cy="7" r="3"/><path d="M5 13h22M16 13v7l-6 9M16 20l6 9"/></svg></div>
<div class="why-ic" style="left:319px;top:3030px"><svg width="32" height="32" viewBox="0 0 32 32" fill="none" stroke="#f25c05" stroke-width="2.4" stroke-dasharray="3 3"><circle cx="16" cy="16" r="11"/></svg></div>
<div class="why-ic" style="left:351px;top:3153px"><svg width="32" height="32" viewBox="0 0 32 32" fill="none" stroke="#f25c05" stroke-width="2.4"><path d="M6 20a10 10 0 0 1 20 0v6H6zM4 26h24"/><circle cx="16" cy="20" r="2"/></svg></div>
<div class="why-ic" style="left:761px;top:2904px"><svg width="32" height="32" viewBox="0 0 32 32" fill="none" stroke="#f25c05" stroke-width="2.4"><circle cx="16" cy="16" r="12"/><circle cx="16" cy="16" r="7"/><circle cx="16" cy="16" r="2"/></svg></div>
<div class="why-ic" style="left:797px;top:3028px"><svg width="32" height="32" viewBox="0 0 32 32" fill="none" stroke="#f25c05" stroke-width="2.4"><path d="M6 18a10 10 0 0 1 20 0M6 18v6h4v-6zM26 18v6h-4v-6zM22 26c0 2-3 3-6 3"/></svg></div>
<div class="why-ic" style="left:761px;top:3153px"><svg width="32" height="32" viewBox="0 0 32 32" fill="none" stroke="#f25c05" stroke-width="2.4"><rect x="4" y="4" width="7" height="7"/><rect x="21" y="4" width="7" height="7"/><rect x="4" y="21" width="7" height="7"/><rect x="21" y="21" width="7" height="7"/><path d="M11 7.5h10M11 24.5h10M7.5 11v10M24.5 11v10"/></svg></div>

<div class="abs testi"></div>
<div class="label" style="left:0;width:1200px;text-align:center;top:3389px">TESTIMONIALS</div>
<div class="sec-title" style="left:0;width:1212px;text-align:center;top:3420px;color:#fff">Client Reviews</div>
<div class="quote" style="left:92px"><span class="qm">&rdquo;</span><p>Lorem ipsum dolor sit amet, consectetur adipiscing elit, sed do eiusmod tem por incididunt ut labore et dolore magna aliqua. Ut enim ad minim veniam, q uis nostrud exercitation ullamco laboris</p><span class="av" role="img" aria-label="Reviewer portrait"></span><span class="nm">Mara K.</span><span class="loc">Zurich</span></div>
<div class="quote" style="left:439px"><span class="qm">&rdquo;</span><p>Lorem ipsum dolor sit amet, consectetur adipiscing elit, sed do eiusmod tem por incididunt ut labore et dolore magna aliqua. Ut enim ad minim veniam, q uis nostrud exercitation ullamco laboris</p><span class="av" role="img" aria-label="Reviewer portrait"></span><span class="nm">Mara K.</span><span class="loc">Zurich</span></div>
<div class="quote" style="left:787px"><span class="qm">&rdquo;</span><p>Lorem ipsum dolor sit amet, consectetur adipiscing elit, sed do eiusmod tem por incididunt ut labore et dolore magna aliqua. Ut enim ad minim veniam, q uis nostrud exercitation ullamco laboris</p><span class="av" role="img" aria-label="Reviewer portrait"></span><span class="nm">Mara K.</span><span class="loc">Zurich</span></div>
<div class="dots"><i></i><i></i><i class="on"></i><i></i><i></i></div>

<div class="abs" style="left:101px;top:3980px;font-weight:600;color:var(--ink);font-size:38px">Contact Us Today</div>
<svg class="cicon" style="top:4058px" viewBox="0 0 38 38" fill="none" stroke="#f25c05" stroke-width="1.6"><path d="M19 4a9 9 0 0 0-9 9c0 7 9 15 9 15s9-8 9-15a9 9 0 0 0-9-9z"/><circle cx="19" cy="13" r="3.5"/><path d="M8 26l-5 9h32l-5-9"/></svg>
<div class="cinfo" style="top:4053px"><b>HEAD OFFICE</b>21 Lorem Ipsum, ABC 123</div>
<svg class="cicon" style="top:4130px" viewBox="0 0 38 38" fill="none" stroke="#f25c05" stroke-width="1.6"><rect x="4" y="10" width="30" height="22"/><path d="M4 10l15 12 15-12M4 32l11-10M34 32L23 22"/></svg>
<div class="cinfo" style="top:4126px"><b>EMAIL ADDRESS</b>21 Lorem Ipsum, ABC 123</div>
<svg class="cicon" style="top:4196px" viewBox="0 0 38 38" fill="none" stroke="#f25c05" stroke-width="1.6"><rect x="11" y="4" width="16" height="30" rx="2"/><path d="M17 29h4M30 14a6 6 0 0 1 0 10"/></svg>
<div class="cinfo" style="top:4192px"><b>CALL US NOW</b>21 Lorem Ipsum, ABC 123</div>

<svg class="abs" style="left:0;top:4330px" width="1200" height="511" viewBox="0 0 1200 511">
  <path d="M0 160 C400 110 800 80 1200 55 L1200 511 L0 511Z" fill="#1b3552"/>
  <path d="M1094 22 L1200 24 L1200 46 L1094 40Z" fill="#f25c05"/>
  <path d="M506 95 L598 82" stroke="#f25c05" stroke-width="4"/>
</svg>

<div class="form">
  <h3>Send Us A Message</h3>
  <label style="left:37px;top:117px">First Name</label>
  <div class="field" style="left:38px;top:137px;width:199px;height:41px">John</div>
  <label style="left:250px;top:117px">Last Name</label>
  <div class="field" style="left:250px;top:137px;width:199px;height:41px">Doe</div>
  <label style="left:37px;top:203px">Email</label>
  <div class="field" style="left:38px;top:223px;width:415px;height:42px">info@lernwandel.ch</div>
  <label style="left:37px;top:293px">Message</label>
  <div class="field area" style="left:38px;top:312px;width:415px;height:122px">Type Your Message</div>
  <div class="btn" style="left:38px;top:475px;width:158px;height:45px;font-size:14px">Contact us
    <svg width="16" height="14" viewBox="0 0 16 14"><path d="M1 7h13M9 2l5 5-5 5" fill="none" stroke="#fff" stroke-width="1.8"/></svg></div>
</div>

<div class="logo" style="left:150px;top:4560px;font-size:40px;line-height:52px">lernwandel</div>
<div class="fdiv" style="left:413px"></div>
<svg class="abs" style="left:430px;top:4618px" width="30" height="30" viewBox="0 0 34 34" fill="none" stroke="#fff" stroke-width="1.8"><circle cx="17" cy="17" r="14"/><ellipse cx="17" cy="17" rx="6" ry="14"/><path d="M3 17h28M5 10h24M5 24h24"/></svg>
<div class="fcontact" style="left:470px">123, Building Name, Street<br>City, State XY 123456</div>
<div class="fdiv" style="left:674px"></div>
<svg class="abs" style="left:688px;top:4615px" width="30" height="34" viewBox="0 0 30 34" fill="none" stroke="#fff" stroke-width="1.8"><rect x="4" y="2" width="14" height="28" rx="2"/><path d="M9 26h4M22 12a5 5 0 0 1 0 9M25 9a9 9 0 0 1 0 15"/></svg>
<div class="fcontact" style="left:727px">PHONE<br>(044) 555 0190</div>
<div class="fdiv" style="left:849px"></div>
<svg class="abs" style="left:866px;top:4620px" width="30" height="26" viewBox="0 0 30 26" fill="none" stroke="#fff" stroke-width="1.8"><rect x="2" y="3" width="26" height="20"/><path d="M2 3l13 10 13-10M2 23l10-9M28 23l-10-9"/></svg>
<div class="fcontact" style="left:905px">EMAIL<br>info@lernwandel.ch</div>

<div class="fnav">
  <span style="left:40px">HOME</span>
  <span style="left:145px">SERVICES</span>
  <span style="left:256px">ABOUT US</span>
  <span style="left:389px">TESTIMONIALS</span>
  <span style="left:509px">BLOG</span>
  <span style="left:626px">CONTACT US</span>
</div>
<div class="abs" style="left:146px;top:4792px;color:#fff;font-size:11px">Lernwandel Apprentice Exchange</div>
<span class="sq" style="left:935px"></span>
<span class="sq" style="left:968px"></span>
<span class="sq" style="left:1001px"></span>
<span class="sq" style="left:1034px"></span>

</body>
</html>
```